Brightfen Business Card Redesign & Logo Update

We need to update our business cards to something more modern and fresh. Brightfen can provide the current color schemes and old design examples, but welcome creativity in helping us with this redesign. PLEASE NOTE that we no longer utilize the "tree" and/or "leaf" imagery in our branding. If able would apprecaite an update on the quality of our "words only" logo in Ai. / PNG formats too.

Target Market(s)

Investors, landowners, corporate partners, contractors

Industry/Entity Type

Environmental Restoration & Conservation

Contact Information for Business Card

Logo, persons name, title, mailing address, phone and email, website url

Font styles to use
Other font styles liked:
• Merriweather

Requirements
Nice to have
• Logo, persons name, title, mailing address, phone and email, website url, but open to ideams
Should not have
• No all back backgrounds

```html
<!DOCTYPE html>
<html lang="en">
<head>
<meta charset="utf-8">
<title>Brightfen Business Card</title>
<link rel="stylesheet" href="https://fonts.googleapis.com/css2?family=Oswald:wght@700&family=Open+Sans:wght@400;700&display=swap">
<style>
  :root {
    --stage: #2a2a2c;
    --orange: #ee8026;
    --green: #13803e;
    --ink: #1c1c1c;
    --band: #232325;
    --paper: #ffffff;
  }
  * { box-sizing: border-box; margin: 0; padding: 0; }
  html, body { width: 1200px; height: 780px; overflow: hidden; }
  body { background: var(--stage); position: relative; font-family: "Open Sans", sans-serif; }

  .card {
    position: absolute;
    width: 540px;
    height: 310px;
    overflow: hidden;
  }

  /* Front */
  .card-front {
    left: 60px; top: 70px;
    background: var(--orange);
    display: flex; align-items: center; justify-content: center;
  }
  .card-front .wordmark {
    font-family: "Oswald", sans-serif;
    font-weight: 700;
    font-size: 104px;
    letter-spacing: 1px;
    text-transform: uppercase;
    color: var(--ink);
    line-height: 1;
  }

  /* Back */
  .card-back {
    left: 600px; top: 400px;
    background: var(--paper);
  }
  .brand-band {
    position: absolute; left: 0; top: 0;
    width: 140px; height: 100%;
    background: var(--band);
  }
  .brand-band .wordmark {
    position: absolute;
    left: 50%; top: 50%;
    transform: translate(-50%, -50%) rotate(-90deg);
    font-family: "Oswald", sans-serif;
    font-weight: 700;
    font-size: 62px;
    text-transform: uppercase;
    color: var(--orange);
    line-height: 1;
    white-space: nowrap;
  }
  .details { position: absolute; left: 172px; right: 28px; top: 0; bottom: 0; }
  .rule { position: absolute; left: 0; right: 0; height: 1px; background: var(--ink); }
  .rule-top { top: 40px; }
  .rule-bottom { top: 116px; }
  .person { position: absolute; left: 0; top: 56px; }
  .person-name { font-weight: 700; font-size: 26px; line-height: 1.1; }
  .person-name .first { color: var(--orange); }
  .person-name .last { color: var(--green); }
  .person-title { font-size: 13px; color: var(--ink); margin-top: 3px; }
  .address { position: absolute; left: 0; top: 160px; font-size: 13px; line-height: 1.5; color: var(--ink); }
  .contacts { position: absolute; left: 0; top: 210px; list-style: none; font-size: 13px; color: var(--ink); }
  .contacts li { display: flex; align-items: center; gap: 8px; line-height: 1.6; }
  .contacts svg { width: 13px; height: 13px; fill: var(--orange); flex: none; }
</style>
</head>
<body>

  <section class="card card-front" aria-label="Card front">
    <span class="wordmark">Brightfen</span>
  </section>

  <section class="card card-back" aria-label="Card back">
    <div class="brand-band">
      <span class="wordmark">Brightfen</span>
    </div>
    <div class="details">
      <div class="rule rule-top"></div>
      <div class="person">
        <p class="person-name"><span class="first">Lena</span> <span class="last">Marsh</span></p>
        <p class="person-title">Managing Director</p>
      </div>
      <div class="rule rule-bottom"></div>
      <p class="address">418 Orchard Ln. Suite 120<br>Denton, TX 76201</p>
      <ul class="contacts">
        <li>
          <svg viewBox="0 0 24 24" aria-hidden="true"><path d="M6.6 10.8a15.1 15.1 0 0 0 6.6 6.6l2.2-2.2a1 1 0 0 1 1-.25 11.4 11.4 0 0 0 3.6.57 1 1 0 0 1 1 1V20a1 1 0 0 1-1 1A17 17 0 0 1 3 4a1 1 0 0 1 1-1h3.5a1 1 0 0 1 1 1c0 1.25.2 2.46.57 3.6a1 1 0 0 1-.25 1z"/></svg>
          (940) 555-0147
        </li>
        <li>
          <svg viewBox="0 0 24 24" aria-hidden="true"><path d="M2 5h20v14H2zm2 2v.5l8 5 8-5V7zm0 2.8V17h16V9.8l-8 5z"/></svg>
          hello@brightfen.com
        </li>
        <li>
          <svg viewBox="0 0 24 24" aria-hidden="true"><path d="M12 2a10 10 0 1 0 0 20 10 10 0 0 0 0-20zm6.9 6h-3a15.7 15.7 0 0 0-1.4-3.6A8 8 0 0 1 18.9 8zM12 4a14 14 0 0 1 1.9 4h-3.8A14 14 0 0 1 12 4zM4.3 14a8.2 8.2 0 0 1 0-4h3.4a16.5 16.5 0 0 0 0 4zm.8 2h3a15.7 15.7 0 0 0 1.4 3.6A8 8 0 0 1 5.1 16zm3-8h-3a8 8 0 0 1 4.4-3.6A15.7 15.7 0 0 0 8.1 8zM12 20a14 14 0 0 1-1.9-4h3.8A14 14 0 0 1 12 20zm2.3-6H9.7a14.7 14.7 0 0 1 0-4h4.6a14.7 14.7 0 0 1 0 4zm.2 5.6a15.7 15.7 0 0 0 1.4-3.6h3a8 8 0 0 1-4.4 3.6zm1.8-5.6a16.5 16.5 0 0 0 0-4h3.4a8.2 8.2 0 0 1 0 4z"/></svg>
          www.brightfen.com
        </li>
      </ul>
    </div>
  </section>

</body>
</html>
```